New Business Card Design Project

Need a design that will create an impact / strong impression towards our clients for our business. We are in the lighting business and we do lighting retrofits for large commercial to industrial clientele.

Target Market(s)

Lighting Industry

Industry/Entity Type

Business

Font styles to use
Other font styles liked:
• we would like to use the font on our logo, not sure what it is though..

Requirements
Must have
• Our logo.
Nice to have
• We are open to suggestions that have to do with lighting.

```html
<!DOCTYPE html>
<html lang="en">
<head>
<meta charset="utf-8">
<title>Lumaris Retrofit Company – Business Card</title>
<link href="https://fonts.googleapis.com/css2?family=Montserrat:wght@600;700;800&family=Open+Sans:wght@400;600&display=swap" rel="stylesheet">
<style>
  :root {
    --green-deep: #0b4f1c;
    --green-main: #0b8a3a;
    --green-mid: #168f3e;
    --green-light: #5cc25a;
    --white: #ffffff;
    --ink: #222222;
    --stage: #eceeea;
  }
  * { box-sizing: border-box; margin: 0; padding: 0; }
  html, body { width: 1200px; height: 900px; overflow: hidden; }
  body {
    background: var(--stage);
    font-family: "Open Sans", Arial, sans-serif;
    position: relative;
  }
  .card {
    position: absolute;
    width: 700px;
    height: 400px;
    border-radius: 4px;
    overflow: hidden;
    box-shadow: 0 10px 30px rgba(0,0,0,0.18);
  }
  /* Back side */
  .card-back {
    left: 90px; top: 110px;
    background: linear-gradient(120deg, var(--green-main) 0%, #13993f 55%, var(--green-light) 100%);
    color: var(--white);
  }
  .card-back .brand {
    position: absolute;
    left: 70px; top: 120px;
    display: flex; align-items: center; gap: 18px;
  }
  .brand-name {
    font-family: "Montserrat", Arial, sans-serif;
    font-weight: 800;
    letter-spacing: 2px;
    line-height: 1;
  }
  .card-back .brand-name { font-size: 76px; color: var(--white); }
  .card-back .brand-square { width: 22px; height: 22px; background: var(--white); }
  .card-back .rule {
    position: absolute; left: 70px; top: 222px;
    width: 560px; height: 2px; background: var(--white);
  }
  .card-back .legal-name {
    position: absolute; left: 70px; top: 234px;
    font-family: "Montserrat", Arial, sans-serif;
    font-weight: 700; font-size: 17px; letter-spacing: 2px;
    text-transform: uppercase;
  }
  /* Front side */
  .card-front {
    left: 420px; top: 400px;
    background: var(--white);
    color: var(--ink);
  }
  .card-front .brand {
    position: absolute; left: 60px; top: 50px;
    display: flex; align-items: center; gap: 16px;
  }
  .card-front .brand-name { font-size: 64px; color: var(--green-main); }
  .card-front .brand-square { width: 20px; height: 20px; background: var(--green-light); }
  .card-front .rule {
    position: absolute; left: 60px; top: 140px;
    width: 520px; height: 2px; background: var(--green-main);
  }
  .person { position: absolute; left: 60px; top: 168px; }
  .person-name {
    font-family: "Montserrat", Arial, sans-serif;
    font-weight: 700; font-size: 22px; color: var(--green-main);
    text-transform: uppercase; letter-spacing: 0.5px;
  }
  .person-role { font-size: 16px; color: var(--ink); margin-top: 2px; }
  .contact-list {
    position: absolute; left: 60px; top: 238px;
    list-style: none; font-size: 16px; line-height: 27px;
  }
  .contact-list li { display: flex; align-items: center; gap: 10px; }
  .contact-list svg { width: 14px; height: 14px; flex: none; }
  .icon-fill { fill: var(--green-main); }
  .icon-line { fill: none; stroke: var(--green-main); stroke-width: 2.4; }
  .address {
    position: absolute; right: 40px; top: 246px;
    text-align: right; font-size: 14px; line-height: 20px;
  }
  .band { position: absolute; bottom: 0; height: 50px; }
  .band-deep  { left: 0; width: 360px; background: var(--green-deep); }
  .band-mid   { left: 360px; width: 190px; background: var(--green-mid); }
  .band-light { left: 550px; width: 150px; background: var(--green-light); }
</style>
</head>
<body>
  <section class="card card-back" aria-label="Card back">
    <div class="brand">
      <span class="brand-name">LUMARIS</span>
      <span class="brand-square"></span>
    </div>
    <div class="rule"></div>
    <p class="legal-name">Lumaris Retrofit Company</p>
  </section>

  <section class="card card-front" aria-label="Card front">
    <div class="brand">
      <span class="brand-name">LUMARIS</span>
      <span class="brand-square"></span>
    </div>
    <div class="rule"></div>

    <div class="person">
      <p class="person-name">Daniel Reyes</p>
      <p class="person-role">Managing Director</p>
    </div>

    <ul class="contact-list">
      <li><svg viewBox="0 0 24 24" aria-hidden="true"><path class="icon-fill" d="M6.6 10.8a15 15 0 0 0 6.6 6.6l2.2-2.2a1 1 0 0 1 1-.25 11.4 11.4 0 0 0 3.6.57 1 1 0 0 1 1 1V20a1 1 0 0 1-1 1A17 17 0 0 1 3 4a1 1 0 0 1 1-1h3.5a1 1 0 0 1 1 1c0 1.25.2 2.45.57 3.57a1 1 0 0 1-.25 1z"/></svg>(044) 555 0142</li>
      <li><svg viewBox="0 0 24 24" aria-hidden="true"><rect class="icon-line" x="2.5" y="5.5" width="19" height="13"/><path class="icon-line" d="M2.5 5.5l9.5 7.5 9.5-7.5"/></svg>hello@lumarisretrofit.com</li>
      <li><svg viewBox="0 0 24 24" aria-hidden="true"><circle class="icon-line" cx="12" cy="12" r="9.5"/><path class="icon-line" d="M2.5 12h19M12 2.5c3 3 3 16 0 19M12 2.5c-3 3-3 16 0 19"/></svg>www.lumarisretrofit.com</li>
    </ul>

    <p class="address">88 Harbor Lane, Suite 4,<br>Westbrook, 40217</p>

    <div class="band band-deep"></div>
    <div class="band band-mid"></div>
    <div class="band band-light"></div>
  </section>
</body>
</html>
```